Sophisticated, clean website reflecting my feminine, playful side to sell my abstract art,

I need a website no more than 3 pages to showcase my paintings, a little about me and some contact info. I do abstracts so looking for something a little edgy, yet feminine and current.
Updates

Hi there, These are some artists websites that I Iike: Marnelvoss.com (I like how airy it is) peterwallombry.com garethpolvens.com (I like how it scrolls) I'll need a place for a photo ( a headshot-i do not have it yet so I'll need to be able to upload that later) as well as an area for my bio. Also, it's important that I will be able to upload any new photos and descriptions easily so it should be user friendly. Lastly, I like in a sunny place so would like to have this seem upbeat and playful as that is how i like to paint. thanks-I'm trying to upload my photos now -

Target Market(s)

ppl ages 35-70 who want large scale art for their homes

Industry/Entity Type

art

Coding

Coded - Design and coding required

Number of Pages Required

3 page

Colors

Designer to choose colors to be used in the design.

Requirements
Must have
• photos of my art, a place for my bio, be easy to reach me. tasteful-nothing too "in your face" -my clients are pretty high end and organized. They like clean lines
Nice to have
• sophisticated background, muted tones in the back-similar clean font throughout-no cursive
Should not have
• too many dark areas. Too many blocks of color. Too serious.

```html
<!DOCTYPE html>
<html lang="en">
<head>
<meta charset="utf-8">
<title>Lena Marrow — Abstract Art</title>
<link rel="stylesheet" href="https://fonts.googleapis.com/css2?family=Crimson+Pro:wght@400;500&family=Poppins:wght@400;500&display=swap">
<style>
  :root {
    --ink: #111111;
    --paper: #ffffff;
    --field: #f1f1f1;
    --accent-rose: #c0705f;
    --arrow-sage: #8fa888;
    --muted: #6b6b6b;
  }
  * { box-sizing: border-box; margin: 0; padding: 0; }
  html, body { width: 1200px; height: 2776px; overflow: hidden; background: var(--paper); }
  body { position: relative; font-family: "Crimson Pro", Georgia, serif; color: var(--ink); }

  /* header */
  .site-header { position: absolute; left: 0; top: 0; width: 1200px; height: 115px; background: var(--paper); box-shadow: 0 8px 24px rgba(0,0,0,0.12); z-index: 2; }
  .brand { position: absolute; left: 32px; top: 20px; width: 326px; text-align: center; font-family: "Poppins", sans-serif; color: var(--ink); }
  .brand-name { font-weight: 500; font-size: 23px; line-height: 28px; letter-spacing: 9px; margin-right: -9px; }
  .brand-rule { width: 274px; height: 1px; background: var(--ink); margin: 4px auto 5px; }
  .brand-handle { font-weight: 400; font-size: 19px; line-height: 22px; letter-spacing: 4px; margin-right: -4px; }
  .main-nav a { position: absolute; top: 28px; font-size: 20px; color: var(--ink); text-decoration: none; letter-spacing: 0.5px; }
  .brand-mark { position: absolute; left: 1010px; top: 34px; font-family: "Poppins", sans-serif; font-weight: 500; font-size: 18px; letter-spacing: 2px; color: var(--ink); }

  .hero-artwork { position: absolute; left: 0; top: 115px; width: 1200px; height: 579px;
    background: linear-gradient(120deg, #9fcf6a 0%, #2f9a4c 30%, #e4dfe8 55%, #48b85a 75%, #1f6f5c 100%);
    box-shadow: 0 10px 30px rgba(0,0,0,0.15); }

  /* about */
  .portrait { position: absolute; left: 182px; top: 767px; width: 286px; height: 286px;
    background: linear-gradient(180deg, #e6e4e3 0%, #d9c7c2 55%, #e57aa2 100%); }
  .bio-eyebrow { position: absolute; left: 619px; top: 790px; font-size: 22px; color: var(--accent-rose); }
  .bio-title { position: absolute; left: 619px; top: 823px; font-size: 33px; font-weight: 400; letter-spacing: 1px; }
  .bio-text { position: absolute; left: 619px; top: 873px; width: 430px; font-size: 17px; line-height: 19.5px; }
  .btn-dark { position: absolute; background: var(--ink); color: var(--paper); display: flex; align-items: center; justify-content: center; }
  .bio-more { left: 619px; top: 987px; width: 108px; height: 30px; font-size: 17px; letter-spacing: 0.5px; }

  /* gallery */
  .section-title { position: absolute; left: 0; width: 1200px; text-align: center; font-weight: 400; }
  .gallery-title { top: 1123px; font-size: 33px; letter-spacing: 1px; }
  .gallery-artwork { position: absolute; left: 177px; top: 1190px; width: 812px; height: 506px;
    background: linear-gradient(115deg, #2f4a3a 0%, #e9e5d8 35%, #3a2a22 50%, #c8682a 65%, #1d9cc4 80%, #cfcfcf 100%); }
  .gallery-arrow { position: absolute; top: 1421px; width: 44px; height: 44px; }
  .artwork-name { top: 1737px; width: 1170px; font-size: 39px; letter-spacing: 1.5px; }
  .artwork-price { position: absolute; left: 0; width: 1170px; top: 1806px; text-align: center; font-family: "Poppins", sans-serif; font-size: 32px; }
  .add-to-cart { left: 484px; top: 1875px; width: 203px; height: 59px; font-family: "Poppins", sans-serif; font-size: 22px; }

  /* follow band */
  .follow-band { position: absolute; left: 0; top: 2008px; width: 1200px; height: 113px; background: var(--ink); color: var(--paper);
    display: flex; align-items: center; justify-content: center; font-size: 41px; letter-spacing: 1.5px; }

  /* contact */
  .contact-title { top: 2210px; font-size: 36px; line-height: 36px; letter-spacing: 1px; }
  .field { position: absolute; left: 382px; width: 443px; background: var(--field); color: var(--muted); font-size: 14px; letter-spacing: 0.5px; text-align: center; }
  .field-short { height: 33px; line-height: 33px; }
  .field-message { height: 75px; padding-top: 4px; }
  .send { left: 560px; top: 2590px; width: 89px; height: 28px; font-size: 14px; letter-spacing: 0.5px; }

  .site-footer { position: absolute; left: 0; top: 2699px; width: 1200px; height: 77px; background: var(--ink); color: var(--paper);
    display: flex; align-items: center; justify-content: center; font-family: "Poppins", sans-serif; font-size: 15px; }
</style>
</head>
<body>
  <header class="site-header">
    <div class="brand">
      <div class="brand-name">LENA MARROW</div>
      <div class="brand-rule"></div>
      <div class="brand-handle">LMARROWART</div>
    </div>
    <nav class="main-nav">
      <a href="#about" style="left:469px">About me</a>
      <a href="#gallery" style="left:625px">Gallery</a>
      <a href="#contact" style="left:761px">Contact us</a>
    </nav>
    <div class="brand-mark">L. MARROW</div>
  </header>

  <div class="hero-artwork" role="img" aria-label="Abstract painting in greens, teal and ochre brushstrokes"></div>

  <section id="about">
    <div class="portrait" role="img" aria-label="Headshot portrait of the artist"></div>
    <p class="bio-eyebrow">Bio Graphy</p>
    <h2 class="bio-title">ABOUT ME</h2>
    <p class="bio-text">Lorem ipsum dolor sit amet, consectetur estor adipi isicing elit, sed do eiusmod tempor este uterre incididui unt ut labore et dolore magna aliquaas. Ut enim ad minim veniam, quis mot nostrud desto exercitation est ullamco laboris nisi ut se aliquip ex ea commodos consequat.</p>
    <div class="btn-dark bio-more">View More</div>
  </section>

  <section id="gallery">
    <h2 class="section-title gallery-title">GALLERY</h2>
    <div class="gallery-artwork" role="img" aria-label="Abstract painting titled The Tidewater, with dark green, white, orange and blue strokes"></div>
    <svg class="gallery-arrow" style="left:111px" viewBox="0 0 44 44" aria-label="Previous">
      <circle cx="22" cy="22" r="22" fill="var(--arrow-sage)"/>
      <path d="M32 22H12M20 14l-8 8 8 8" fill="none" stroke="#fff" stroke-width="2.4" stroke-linecap="round" stroke-linejoin="round"/>
    </svg>
    <svg class="gallery-arrow" style="left:1000px" viewBox="0 0 44 44" aria-label="Next">
      <circle cx="22" cy="22" r="22" fill="var(--arrow-sage)"/>
      <path d="M12 22h20M24 14l8 8-8 8" fill="none" stroke="#fff" stroke-width="2.4" stroke-linecap="round" stroke-linejoin="round"/>
    </svg>
    <h3 class="section-title artwork-name">THE TIDEWATER</h3>
    <p class="artwork-price">$300.</p>
    <div class="btn-dark add-to-cart">ADD TO CARD</div>
  </section>

  <div class="follow-band">FOLLOW LMARROWART ON PICTOGRAM</div>

  <section id="contact">
    <h2 class="section-title contact-title">Fill the form get in<br>touch with me</h2>
    <div class="field field-short" style="top:2320px">Enter your name here</div>
    <div class="field field-short" style="top:2376px">Enter your email here</div>
    <div class="field field-short" style="top:2435px">Enter your phone here</div>
    <div class="field field-message" style="top:2490px">Enter your message here</div>
    <div class="btn-dark send">SEND</div>
  </section>

  <footer class="site-footer">Copyright lmarrowart 2021 All Rights Reserved</footer>
</body>
</html>
```